Meadow Gate Labradoodle web design

We're a new labradoodle breeder in Charleston, SC in need of a web design.

Our name is Meadow Gate Labradoodles.

Site we like: http://www.pebblefieldlabradoodles.com/
http://www.quillbrookfarmlabradoodles.com/

Logo Font:
The ''Meadow Gate'' font is called TestarossaNF and is available freely at http://www.glyphtrove.com/velmorina-nf.font.  The ''Labradoodles'' font is called Worstveld Sling Extra and is available freely at http://www.typebasketzone.com/KorvandelHookExtra.php.

Requirements
Must have
• Our logo
1. Home page
2. Labradoodle F.A.Q.
3. Our doodles
4. Availability
5. Adoption Process
6. Contact us
Link/badge icon for Health Guarantee
Nice to have
• Color and font to match the logo.

An area to add pictures
Should not have
• Rainbows
Rainbow colors

```html
<!DOCTYPE html>
<html lang="en">
<head>
<meta charset="utf-8">
<title>Meadow Gate Labradoodles</title>
<link href="https://fonts.googleapis.com/css2?family=Federant&family=Fjalla+One&family=Ubuntu:wght@300;400;500&display=swap" rel="stylesheet">
<style>
:root{
  --pink:#e2607a;
  --brown:#6b4a2c;
  --tan:#dcc0a3;
  --tan-dark:#b89877;
  --wood-dark:#3a3a38;
  --wood-mid:#55544f;
  --text:#6e6a66;
  --rule:#d8d4d0;
  --footer:#5d5c5a;
  --footer-text:#ecebea;
  --dog:#b77e4c;
}
*{margin:0;padding:0;box-sizing:border-box}
html,body{width:1200px;height:909px;overflow:hidden;background:#fff}
body{position:relative;font-family:'Ubuntu',sans-serif;font-weight:300;color:var(--text)}
.abs{position:absolute}
.header-band{left:0;top:0;width:1200px;height:102px;
  background:repeating-linear-gradient(180deg,rgba(0,0,0,.18) 0 1px,transparent 1px 25px),
  linear-gradient(180deg,var(--wood-mid),var(--wood-dark) 55%,var(--wood-mid))}
.hero{left:0;top:102px;width:1200px;height:300px;
  background:linear-gradient(180deg,#c9c9c7 0%,#dededd 45%,#f4f4f4 80%,#fff 100%)}
.brand{left:196px;top:10px;display:flex;align-items:center;gap:10px}
.brand-mark{width:70px;height:70px;border-radius:50%;background:var(--pink);border:4px solid #f3e4d6}
.brand-name{font-family:'Federant',serif;font-size:20px;line-height:1.15;color:#f3e4d6;width:150px}
.nav{right:205px;top:63px;display:flex;gap:2px}
.nav a{display:block;height:38px;line-height:38px;padding:0 10px;background:linear-gradient(180deg,#2a2a2a,#0d0d0d);
  color:#f2f0ee;text-decoration:none;font-family:'Fjalla One',sans-serif;font-size:14px;border-radius:2px;
  box-shadow:0 1px 0 rgba(255,255,255,.15) inset;white-space:nowrap}
.headline{left:196px;top:158px;font-family:'Federant',serif;font-size:40px;line-height:42px;color:var(--pink);width:380px}
.subhead{left:196px;top:257px;font-family:'Federant',serif;font-style:italic;font-size:18px;color:var(--pink)}
.hero-copy{left:196px;top:283px;width:296px;font-size:9.5px;line-height:11.6px;font-weight:400;color:#5a5652}
.btn{display:inline-block;background:var(--tan);color:var(--brown);font-family:'Federant',serif;font-style:italic;
  font-size:12px;padding:5px 11px;border-radius:3px;box-shadow:0 3px 0 var(--tan-dark)}
.dog-photo{left:688px;top:120px;width:164px;height:272px;border-radius:50% 50% 40% 40%/30% 30% 20% 20%;
  background:radial-gradient(ellipse at 50% 40%,#c99463,var(--dog) 60%,rgba(183,126,76,0) 75%)}
.dots{left:937px;top:367px;display:flex;gap:4px}
.dots span{width:12px;height:12px;border-radius:50%;background:#cfcfcf}
.dots span:first-child{background:var(--pink)}
.col-title{font-family:'Federant',serif;color:var(--brown);font-size:19px;line-height:23px}
.benefits{left:198px;top:436px;width:200px}
.benefits ul{list-style:none;margin-top:11px;width:164px}
.benefits li{position:relative;padding:4px 0 4px 15px;font-size:10.5px;line-height:13.5px;border-bottom:1px dotted var(--rule)}
.benefits li:last-child{border:0}
.paw{position:absolute;left:0;top:7px}
.divider{top:456px;height:192px;border-left:1px dotted var(--rule)}
.welcome{left:455px;top:436px;width:232px}
.welcome p{margin-top:13px;font-size:10.5px;line-height:13.4px}
.welcome .btn{margin-top:11px}
.principles{left:750px;top:438px;width:246px}
.principle{position:relative;padding-left:24px;margin-bottom:14px}
.principle h3{font-family:'Federant',serif;color:var(--brown);font-size:14px;font-weight:400}
.principle p{font-size:10.5px;line-height:13.4px;margin-top:5px}
.principle .paw{top:0}
.principles .btn{margin-left:24px;margin-top:-2px}
.badge{left:931px;top:678px}
.footer{left:0;top:726px;width:1200px;height:183px;background:var(--footer);color:var(--footer-text)}
.f-title{font-family:'Federant',serif;font-size:17px;color:#fff}
.f-col{top:22px}
.f-gallery{left:198px;width:205px}
.f-gallery p{font-size:9px;line-height:11.4px;margin:10px 0 15px;font-weight:400}
.f-links{left:451px;width:125px}
.f-links a{display:block;color:var(--footer-text);text-decoration:none;font-size:11px;padding:4px 0 5px;border-bottom:1px dotted #7d7c7a}
.f-links a:last-child{border:0}
.f-links .f-title{margin-bottom:4px}
.f-connect{left:630px;width:200px}
.socials{display:flex;gap:7px;margin-top:8px}
.socials span{width:25px;height:25px;border-radius:50%;background:var(--pink)}
.f-connect h4{font-family:'Ubuntu',sans-serif;font-weight:400;font-size:16px;margin-top:6px;color:#fff}
.f-connect small{display:block;font-size:9.5px;color:#9c9b98;text-transform:uppercase}
.signup{display:flex;margin-top:1px}
.signup span{width:146px;height:20px;background:#fff;border-radius:2px 0 0 2px}
.signup b{width:46px;height:20px;line-height:20px;background:var(--pink);color:#fff;font-weight:400;font-size:10px;text-align:center}
.f-contact{left:878px;top:28px;width:170px}
.f-contact address{font-style:normal;font-size:11px;line-height:14.6px;margin-top:8px}
.f-div{top:30px;height:140px;border-left:1px dotted #7d7c7a}
.copyright{left:0;top:161px;width:1200px;text-align:center;font-size:9px;font-weight:400}
</style>
</head>
<body>
<svg width="0" height="0" style="position:absolute"><defs>
<g id="paw" fill="#e2607a"><ellipse cx="8" cy="11" rx="4" ry="3.4"/><circle cx="3" cy="6" r="1.9"/><circle cx="6.5" cy="2.8" r="1.9"/><circle cx="10.5" cy="3" r="1.9"/><circle cx="13.5" cy="6.5" r="1.9"/></g>
</defs></svg>

<div class="abs header-band"></div>
<div class="abs hero"></div>

<div class="abs brand">
  <div class="brand-mark"></div>
  <div class="brand-name">Meadow Gate Labradoodles</div>
</div>

<nav class="abs nav">
  <a href="#">LABRADOODLE F.A.Q.</a><a href="#">OUR LABRADOODLES</a><a href="#">AVAILABLE</a><a href="#">PROGRAM</a><a href="#">PROCESS</a><a href="#">CONTACT</a>
</nav>

<h1 class="abs headline">Experience Love At First Cuddle</h1>
<h2 class="abs subhead">Why We are Different</h2>
<p class="abs hero-copy">As premier Australian multi-gen labradoodle breeders in Charleston, SC, we take our labradoodle puppies seriously! Our dogs are a part of our family and live indoors. Every labradoodle puppy has completed health testing and we strive for proper temperament, ability and conformation.</p>
<a class="abs btn" style="left:196px;top:350px">Enquire Now</a>

<div class="abs dog-photo" role="img" aria-label="Photo of a seated apricot labradoodle puppy"></div>
<div class="abs dots"><span></span><span></span><span></span><span></span></div>

<section class="abs benefits">
  <h2 class="col-title">Benefits for the Pet</h2>
  <ul>
    <li><svg class="paw" width="10" height="10" viewBox="0 0 16 15"><use href="#paw"/></svg>24 Hour Contact with sitter.</li>
    <li><svg class="paw" width="10" height="10" viewBox="0 0 16 15"><use href="#paw"/></svg>Provide documentation about daily activities with your pet.</li>
    <li><svg class="paw" width="10" height="10" viewBox="0 0 16 15"><use href="#paw"/></svg>Give medication on time.</li>
    <li><svg class="paw" width="10" height="10" viewBox="0 0 16 15"><use href="#paw"/></svg>Less stress being in their own quiet, familiar environment.</li>
    <li><svg class="paw" width="10" height="10" viewBox="0 0 16 15"><use href="#paw"/></svg>Routine stays the same.</li>
    <li><svg class="paw" width="10" height="10" viewBox="0 0 16 15"><use href="#paw"/></svg>Pet is not exposed to illnesses or fleas.</li>
    <li><svg class="paw" width="10" height="10" viewBox="0 0 16 15"><use href="#paw"/></svg>Personal attention, love and affection.</li>
  </ul>
</section>

<div class="abs divider" style="left:425px"></div>
<div class="abs divider" style="left:720px"></div>

<section class="abs welcome">
  <h2 class="col-title">Welcome Labradoodle Lovers</h2>
  <p>As multi-gen labradoodle breeders in Charleston, SC, we specialize in allergy-friendly, non-shedding Multigen Australian Labradoodles. We choose to breed just a few, select mini and medium labradoodle puppy litters each year. We offer lifetime support on all labradoodle puppies and you can be certain that our two little girls will properly socialize your labradoodle puppy before it's placed into your arms.<br>We have a whimsical, silly outlook on life and we like to think that our labradoodle dogs.</p>
  <a class="btn">Read More</a>
</section>

<section class="abs principles">
  <div class="principle"><svg class="paw" width="17" height="16" viewBox="0 0 16 15"><use href="#paw"/></svg><h3>Our Principles</h3><p>Our strong prinicples are the slogan of Brightpaw Pet Sitting. We deliver personable, expert services with a high degree of integrity.</p></div>
  <div class="principle"><svg class="paw" width="17" height="16" viewBox="0 0 16 15"><use href="#paw"/></svg><h3>Labradoodle Love</h3><p>We are all God's creations. Pets need care and unconditional love.</p></div>
  <div class="principle"><svg class="paw" width="17" height="16" viewBox="0 0 16 15"><use href="#paw"/></svg><h3>Testimonials</h3><p>If you are stll on the fence, listen to the feedback of previous clients and what they thought of Brightpaw Pet Sitting.</p></div>
  <a class="btn">Read More</a>
</section>

<svg class="abs badge" width="64" height="64" viewBox="0 0 64 64" role="img" aria-label="Health guarantee badge">
  <circle cx="32" cy="32" r="31" fill="#c9a23a"/>
  <circle cx="32" cy="32" r="25" fill="#e8c65a"/>
  <circle cx="32" cy="32" r="19" fill="#2b2b2b"/>
</svg>

<footer class="abs footer">
  <div class="abs f-col f-gallery">
    <h2 class="f-title">Gallery</h2>
    <p>Much like our children, our pets are unique with their own personalities. We celebrate the uniqueness of all of our pets through an owner-inspired "growllerly". Enjoy!</p>
    <a class="btn">Enquire Now</a>
  </div>
  <div class="abs f-div" style="left:422px"></div>
  <div class="abs f-col f-links">
    <h2 class="f-title">Links</h2>
    <a href="#">Board of Directors</a><a href="#">Dog Park Rules</a><a href="#">Map</a><a href="#">Education</a>
  </div>
  <div class="abs f-div" style="left:602px"></div>
  <div class="abs f-col f-connect">
    <h2 class="f-title">Connect With us</h2>
    <div class="socials"><span aria-label="Social link"></span><span aria-label="Social link"></span><span aria-label="News feed"></span></div>
    <h4>Newsletter</h4>
    <small>Your email address</small>
    <div class="signup"><span></span><b>SEND</b></div>
  </div>
  <div class="abs f-div" style="left:848px"></div>
  <div class="abs f-contact">
    <h2 class="f-title">Contact Us</h2>
    <address>Linden Row 14<br>29401 Charleston<br>South Carolina<br>+1 843 555 0172<br>hello@meadowgatedoodles.com</address>
  </div>
  <p class="abs copyright">Copyright © 2012 ~ All Rights Reserved ~ We are proud to be a responsible Charleston, SC Multigen Labradoodle Puppy Breeder!</p>
</footer>
</body>
</html>
```